Yacht, Boats, Watersports company needs a redesign of business card

Hello Designers!
We are a Boat dealership company that sells fun in the water, we sell boats, Yachts, Kayaks and also yacht WaterSport toys. We are looking to redesign our business cards in to something a little bit more sophisticated. in a way that we can make better use of our company colors. I'm attaching a zipped file containing the company 3 sets of company logo which one is an horizontal another one is a vertical and also a chromed 3d logo. Also is included two set of business cards that we use and also some designs that i think it's interesting. We use PMS 2026c Orange and PMS 7687C Blue. I would like to see at least two different options with the orange as accent and also using blue as an accent color. It's really important for the business cards to have a font option and size that is legible to most people. Our current website is wwww.coralpennant.com. Please visit if you want to have a better feeling of the Boat dealership
You can send Single sided or double side options. We are now using single sided but we may be open for a double side option if we really like the design.
Target Market(s)
Marine, boat sales, yacht sales, water toys sales/
Contact Information for Business Card
Name: Dale Whitcombe
Address: 212 North Fenwick Lane,
Marlin Bay, FL 33071
Phone: 954-731-8842
Fax: 954:731-8843
Cell: 954-382-1490
Email: dw@coralpennant.com
Website: coralpennant.com
Requirements
Must have
- the current information of the business card provided.
logo
use the PMS Colors
Nice to have
- a touch of elegance and sophistication but simple
Should not have
- should not have any typography that is hard to read, the card should be simple but yet sophisticated.

```html
<!DOCTYPE html>
<html lang="en">
<head>
<meta charset="UTF-8">
<title>Coral Pennant – Business Card</title>
<link href="https://fonts.googleapis.com/css2?family=Poppins:wght@400;500&display=swap" rel="stylesheet">
<style>
  :root {
    --backdrop: #e4e4e4;
    --card-white: #ffffff;
    --brand-blue: #2a6cb4;
    --brand-blue-deep: #1c5ca6;
    --brand-blue-light: #3a86c6;
    --brand-orange: #f08a24;
    --text-grey: #555a60;
    --rule-grey: #6b6b6b;
  }
  * { margin: 0; padding: 0; box-sizing: border-box; }
  html, body { width: 1200px; height: 1200px; overflow: hidden; }
  body { background: var(--backdrop); font-family: "Poppins", sans-serif; }
  .stage { position: relative; width: 1200px; height: 1200px; }

  .card {
    position: absolute; left: 262px; width: 686px; height: 392px;
    border-radius: 18px; overflow: hidden;
  }
  .card-front { top: 165px; background: var(--card-white); }
  .card-back {
    top: 653px;
    background: linear-gradient(135deg, var(--brand-blue-deep) 0%, var(--brand-blue) 55%, var(--brand-blue-light) 100%);
  }

  /* front: brand block */
  .brand { position: absolute; left: 40px; top: 0; width: 300px; height: 392px; text-align: center; }
  .brand-dot {
    position: absolute; left: 112px; top: 122px; width: 76px; height: 76px;
    border-radius: 50%; border: 6px solid var(--brand-blue);
  }
  .brand-name {
    position: absolute; left: 0; right: 0; top: 212px;
    font-weight: 500; font-size: 24px; letter-spacing: 0.5px; color: var(--brand-blue);
    text-transform: uppercase; line-height: 1.15;
  }

  .divider { position: absolute; left: 354px; top: 107px; width: 1px; height: 174px; background: var(--rule-grey); }

  /* front: contact block */
  .contact { position: absolute; left: 383px; top: 102px; color: var(--text-grey); }
  .contact-name { font-weight: 500; font-size: 22px; color: var(--brand-blue); letter-spacing: 0.3px; line-height: 1.2; }
  .contact-address { margin-top: 8px; font-size: 15.5px; line-height: 19px; }
  .contact-lines { margin-top: 10px; list-style: none; font-size: 15.5px; line-height: 19.5px; }
  .contact-lines li { display: flex; align-items: center; gap: 9px; }
  .contact-lines svg { width: 14px; height: 14px; fill: var(--brand-blue); flex: none; }

  .band { position: absolute; bottom: 0; height: 14px; }
  .band-blue { left: 0; width: 339px; background: var(--brand-blue); }
  .band-orange { left: 343px; right: 0; background: var(--brand-orange); }

  /* back */
  .back-brand {
    position: absolute; left: 0; right: 0; top: 163px; height: 48px;
    display: flex; align-items: center; justify-content: center; gap: 14px;
  }
  .back-dot { width: 40px; height: 40px; border-radius: 50%; background: #ffffff; flex: none; }
  .back-name { font-weight: 500; font-size: 32px; color: #ffffff; letter-spacing: 1px; line-height: 44px; }
  .back-web {
    position: absolute; left: 0; right: 0; top: 342px; text-align: center;
    font-size: 16px; letter-spacing: 3.6px; color: #ffffff; line-height: 22px;
  }
</style>
</head>
<body>
<main class="stage">
  <section class="card card-front">
    <div class="brand">
      <div class="brand-dot"></div>
      <div class="brand-name">Coral Pennant<br>Marine Center</div>
    </div>
    <div class="divider"></div>
    <div class="contact">
      <h1 class="contact-name">DALE WHITCOMBE</h1>
      <p class="contact-address">212 North Fenwick Lane<br>Marlin Bay, FL 33071</p>
      <ul class="contact-lines">
        <li><svg viewBox="0 0 24 24"><path d="M6.6 10.8a15.1 15.1 0 0 0 6.6 6.6l2.2-2.2a1 1 0 0 1 1-.25 11.4 11.4 0 0 0 3.6.57 1 1 0 0 1 1 1V20a1 1 0 0 1-1 1A17 17 0 0 1 3 4a1 1 0 0 1 1-1h3.5a1 1 0 0 1 1 1c0 1.250.2 2.45.57 3.57a1 1 0 0 1-.25 1z"/></svg>954-731-8842</li>
        <li><svg viewBox="0 0 24 24"><path d="M7 1h10a2 2 0 0 1 2 2v18a2 2 0 0 1-2 2H7a2 2 0 0 1-2-2V3a2 2 0 0 1 2-2zm0 3v15h10V4z"/></svg>954-382-1490</li>
        <li><svg viewBox="0 0 24 24"><path d="M6 2h9l3 3v5H6zM3 11h18a1 1 0 0 1 1 1v9H2v-9a1 1 0 0 1 1-1zm3 4v2h12v-2z"/></svg>954:731-8843</li>
        <li><svg viewBox="0 0 24 24"><path d="M2 5h20v14H2zm2 2v.5l8 5 8-5V7l-8 5z"/></svg>dw@coralpennant.com</li>
        <li><svg viewBox="0 0 24 24"><path d="M12 2a10 10 0 1 0 0 20 10 10 0 0 0 0-20zm-1 17.9A8 8 0 0 1 4.2 10L9 14.8v1a2 2 0 0 0 2 2zm6.9-2.5A2 2 0 0 0 16 16h-1v-3a1 1 0 0 0-1-1H8v-2h2a1 1 0 0 0 1-1V7h2a2 2 0 0 0 2-2v-.4a8 8 0 0 1 2.9 12.8z"/></svg>coralpennant.com</li>
      </ul>
    </div>
    <div class="band band-blue"></div>
    <div class="band band-orange"></div>
  </section>

  <section class="card card-back">
    <div class="back-brand">
      <div class="back-dot"></div>
      <div class="back-name">CORAL PENNANT</div>
    </div>
    <p class="back-web">WWW.CORALPENNANT.COM</p>
  </section>
</main>
</body>
</html>
```